Patent Law

Need to develop a home page for a patent lawyer.

Colors should go with logo, blues...

Company Name- Velun Tresk, PLLC

Company Overview-

I am an Intellectual Property Lawyer and focus on patents, copyrights, trademarks, & trade secrets. I work with small businesses and start ups in the chemical and biotech industries.

Why Us-

I am small firm that can provide large-firm service at a reasonable price. I also can charge flat-fees for entreprenuers in certain practice areas.

Services-
Intellectual Property
Patents
Copyrights
Trademarks
Trade secrets
Healthcare Compliance
Elder law
Wills
Trusts

Website we like-
http://www.quorvantlegal.example/ - within industry!!
http://www.daltrowemiko.example/
http://ulbrixtane.example/
http://thegravelcounsel.example/

Target Market(s)

My customers will be small business, specifically small start-up companies in the chemical and biotech arena.

Industry/Entity Type

Trade

Requirements
Must have
• Colors should go with logo, blues...

```html
<!DOCTYPE html>
<html lang="en">
<head>
<meta charset="utf-8">
<title>Velun Tresk, PLLC — Intellectual Property Law</title>
<link rel="stylesheet" href="https://fonts.googleapis.com/css2?family=Arimo:wght@400;700&family=Oxygen:wght@400&display=swap">
<style>
  :root {
    --page-bg: #f1f1f1;
    --top-rule: #555555;
    --brand-blue: #1a86dc;
    --brand-blue-dark: #0d62b0;
    --accent-blue: #1b8be0;
    --text-grey: #6d6d6d;
    --text-dark: #4a4a4a;
    --tab-bg: #e2e3e4;
    --tab-active: #efeeee;
    --footer-bg: #434343;
    --white: #ffffff;
  }
  * { box-sizing: border-box; margin: 0; padding: 0; }
  html, body { width: 1049px; height: 1200px; overflow: hidden; }
  body {
    background: var(--page-bg);
    font-family: "Arimo", Arial, sans-serif;
    color: var(--text-grey);
    position: relative;
  }
  .abs { position: absolute; }

  .top-rule { left: 0; top: 0; width: 1049px; height: 8px; background: var(--top-rule); }

  /* Header */
  .brand { left: 72px; top: 96px; font-size: 14px; letter-spacing: 1px; color: var(--text-dark); text-transform: uppercase; }
  .brand-mark { left: 112px; top: 42px; width: 46px; height: 46px; border-radius: 50%; background: var(--brand-blue-dark); }
  .social { left: 853px; top: 34px; display: flex; gap: 7px; }
  .social span { width: 26px; height: 26px; border-radius: 4px; background: linear-gradient(#4aa2e6, #1c6fc0); display: block; }
  .contact-icon { left: 853px; }
  .contact-label { left: 876px; font-size: 12px; letter-spacing: 1px; color: var(--text-dark); }
  .contact-phone { left: 877px; top: 86px; font-size: 12px; letter-spacing: 1px; color: var(--accent-blue); }

  /* Navigation */
  .main-nav { left: 0; top: 140px; width: 1049px; height: 40px; background: linear-gradient(#2b8fdc, #1473c4 60%, #0f66b3); }
  .nav-item { top: 12px; font-size: 14px; letter-spacing: 1.2px; color: var(--white); text-transform: uppercase; }
  .nav-item.is-current { top: 8px; left: 59px; width: 62px; height: 24px; padding-top: 4px; text-align: center; background: rgba(255,255,255,0.25); border-radius: 2px; }
  .search { left: 829px; top: 8px; width: 117px; height: 24px; background: var(--white); border-radius: 3px 0 0 3px; font-size: 13px; letter-spacing: 1px; color: #9a9a9a; padding: 5px 0 0 11px; }
  .search-btn { left: 946px; top: 8px; width: 52px; height: 24px; background: linear-gradient(#9a9a9a, #6a6a6a); border-radius: 0 3px 3px 0; }

  /* Hero */
  .hero-shadow { left: 50px; top: 625px; width: 945px; height: 30px; background: radial-gradient(ellipse at 20% 0%, rgba(0,0,0,0.18), transparent 60%), radial-gradient(ellipse at 80% 0%, rgba(0,0,0,0.18), transparent 60%); }
  .hero { left: 43px; top: 201px; width: 959px; height: 426px; background: #ebebeb; box-shadow: 0 2px 6px rgba(0,0,0,0.12); }
  .hero-photo { left: 11px; top: 10px; width: 645px; height: 340px; background: radial-gradient(circle at 62% 78%, #ffffff 0%, #eef2fb 18%, transparent 42%), linear-gradient(180deg, #5f80c8 0%, #9cb1e2 40%, #d9e2f6 75%, #eef2fb 100%); }
  .hero-rock { left: 11px; top: 480px; }
  .hero-panel { left: 656px; top: 10px; width: 294px; height: 340px; background: linear-gradient(180deg, #2585e0, #0d5fb8); color: var(--white); }
  .hero-notch { left: 618px; top: 25px; }
  .hero-title { left: 0; top: 46px; width: 100%; text-align: center; font-weight: 700; letter-spacing: 1.5px; }
  .hero-title .line-1 { display: block; font-size: 19px; }
  .hero-title .line-2 { display: block; font-size: 15px; margin-top: 3px; }
  .hero-copy { left: 39px; top: 104px; width: 245px; font-size: 12.5px; line-height: 15.4px; letter-spacing: 0.9px; text-align: justify; }
  .hero-copy p + p { margin-top: 15px; }

  .practice-tabs { left: 11px; top: 350px; width: 939px; height: 66px; background: var(--tab-bg); border-top: 1px solid #d6d6d6; }
  .practice-tab { top: 20px; width: 110px; margin-left: -55px; text-align: center; font-family: "Oxygen", Arial, sans-serif; font-size: 12px; line-height: 15px; letter-spacing: 0.5px; color: #6a6a6a; text-transform: uppercase; }
  .practice-tab.is-active { color: var(--accent-blue); }
  .tab-active-bg { left: 358px; top: 0; width: 100px; height: 66px; background: var(--tab-active); }
  .tab-pointer { left: 385px; top: -33px; }

  /* Feature cards */
  .features-shadow { left: 50px; top: 1082px; width: 945px; height: 30px; background: radial-gradient(ellipse at 20% 0%, rgba(0,0,0,0.16), transparent 60%), radial-gradient(ellipse at 80% 0%, rgba(0,0,0,0.16), transparent 60%); }
  .features { left: 41px; top: 668px; width: 966px; height: 417px; border: 1px solid #dcdcdc; border-radius: 5px; background: repeating-linear-gradient(135deg, #efefef 0 2px, #eaeaea 2px 4px); }
  .card { top: 49px; width: 278px; height: 320px; }
  .card-strip { left: 0; top: 0; width: 278px; height: 8px; background: var(--accent-blue); }
  .card-notch { left: 134px; top: 8px; }
  .card-photo { left: 0; top: 8px; width: 278px; height: 184px; }
  .photo-puzzle { background: linear-gradient(160deg, #6f8ed0, #3a5fa8 55%, #1e3f82); }
  .photo-bulbs { background: radial-gradient(circle at 63% 35%, #c7cfe6, #4a5c8c 40%, #1e2a4c); }
  .photo-news { background: linear-gradient(120deg, #2c2c2c 0 12%, #d8d8d8 30%, #f4f4f4 60%, #e2ded6); }
  .card-title { left: 0; top: 204px; font-size: 15px; font-weight: 700; letter-spacing: 1.2px; color: var(--accent-blue); text-transform: uppercase; }
  .card-text { left: 2px; top: 230px; width: 272px; font-size: 12.5px; line-height: 15.4px; letter-spacing: 0.9px; color: var(--text-grey); text-align: justify; }
  .card-rule { left: 0; top: 308px; width: 282px; height: 1px; background: #bdbdbd; }
  .read-more { top: 297px; width: 76px; height: 24px; border-radius: 3px; background: linear-gradient(#2e97e8, #1176d1); color: var(--white); font-size: 12.5px; letter-spacing: 0.8px; text-align: center; padding-top: 5px; }

  /* Footer */
  .site-footer { left: 0; top: 1157px; width: 1049px; height: 43px; background: repeating-linear-gradient(0deg, #444 0 2px, #3e3e3e 2px 3px); color: #e6e6e6; font-size: 11px; letter-spacing: 1px; }
  .copyright { left: 81px; top: 16px; }
  .footer-links { right: 68px; top: 16px; word-spacing: 2px; }
  .footer-links span.sep { margin: 0 10px; }
</style>
</head>
<body>
  <div class="abs top-rule"></div>

  <header>
    <div class="abs brand-mark"></div>
    <div class="abs brand">Velun Tresk, PLLC</div>

    <div class="abs social" aria-label="Social links"><span></span><span></span><span></span><span></span></div>

    <svg class="abs contact-icon" style="top:72px" width="18" height="18" viewBox="0 0 18 18" aria-hidden="true">
      <path d="M4 2 L7 5 L5.5 7.5 Q8 11 10.5 12.5 L13 11 L16 14 L13.5 16.5 Q7 15 1.5 4.5 Z" fill="#1b8be0"/>
    </svg>
    <div class="abs contact-label" style="top:72px">CALL US TODAY</div>
    <div class="abs contact-phone">(02)-5550-10987</div>

    <svg class="abs contact-icon" style="top:104px;left:856px" width="14" height="19" viewBox="0 0 14 19" aria-hidden="true">
      <path d="M7 1 C3.5 1 1 3.5 1 6.8 C1 11 7 18 7 18 C7 18 13 11 13 6.8 C13 3.5 10.5 1 7 1 Z" fill="#1b8be0"/>
      <circle cx="7" cy="7" r="2.3" fill="#f1f1f1"/>
    </svg>
    <div class="abs contact-label" style="top:105px">MAP &amp; DIRECTIONS</div>
  </header>

  <nav class="abs main-nav">
    <div class="abs nav-item is-current">Home</div>
    <div class="abs nav-item" style="left:160px">About Us</div>
    <div class="abs nav-item" style="left:285px">Services</div>
    <div class="abs nav-item" style="left:413px">Latest News</div>
    <div class="abs nav-item" style="left:572px">Contact Us</div>
    <div class="abs search">Search</div>
    <div class="abs search-btn">
      <svg width="52" height="24" viewBox="0 0 52 24" aria-hidden="true">
        <circle cx="23" cy="10" r="4" fill="none" stroke="#222" stroke-width="2"/>
        <line x1="26" y1="13" x2="31" y2="17" stroke="#222" stroke-width="2.5" stroke-linecap="round"/>
      </svg>
    </div>
  </nav>

  <div class="abs hero-shadow"></div>
  <section class="abs hero">
    <div class="abs hero-photo" role="img" aria-label="Photo of a man with raised arms standing on a rock against a bright blue sky over the sea"></div>
    <div class="abs hero-panel">
      <h1 class="abs hero-title"><span class="line-1">HEADLINE TEXT HERE</span><span class="line-2">second line goes here</span></h1>
      <div class="abs hero-copy">
        <p>Lorem ipsum dolor sit amet, consectetur adipiscing elit. Nullam elementum hendrerit nisl, ut tempor leo cursus ut. Quisque tincidunt velit sit amet blandit convallis. Nulla adipiscing nisl scelerisque, porttitor est eget,</p>
        <p>condimentum ante. Aenean sit amet lacus eu justo mattis semper. Quisque tellus purus, sagittis eget nibh ac, interdum congue augue. Morbi ultrices pretium varius.</p>
      </div>
    </div>
    <svg class="abs hero-notch" width="40" height="44" viewBox="0 0 40 44" aria-hidden="true">
      <polygon points="0,22 40,0 40,44" fill="#2585e0"/>
    </svg>

    <div class="abs practice-tabs">
      <div class="abs tab-active-bg"></div>
      <svg class="abs tab-pointer" style="left:396px" width="36" height="34" viewBox="0 0 36 34" aria-hidden="true">
        <polygon points="18,0 36,34 0,34" fill="#efeeee"/>
      </svg>
      <div class="abs practice-tab" style="left:87px">Intellectual<br>Property</div>
      <div class="abs practice-tab" style="left:203px">Healthcare<br>Compliance</div>
      <div class="abs practice-tab" style="left:302px">Trade<br>Secrets</div>
      <div class="abs practice-tab is-active" style="left:406px">Trademarks</div>
      <div class="abs practice-tab" style="left:521px">Copyrights</div>
      <div class="abs practice-tab" style="left:622px">Patents</div>
      <div class="abs practice-tab" style="left:715px">Elder<br>Law</div>
      <div class="abs practice-tab" style="left:793px">Wills</div>
      <div class="abs practice-tab" style="left:867px">Trusts</div>
    </div>
  </section>

  <div class="abs features-shadow"></div>
  <section class="abs features">
    <article class="abs card" style="left:38px">
      <div class="abs card-photo photo-puzzle" role="img" aria-label="Photo of blue jigsaw puzzle pieces with one piece missing"></div>
      <div class="abs card-strip"></div>
      <svg class="abs card-notch" width="14" height="8" viewBox="0 0 14 8" aria-hidden="true"><polygon points="0,0 14,0 7,8" fill="#1b8be0"/></svg>
      <h2 class="abs card-title">About Velun Tresk</h2>
      <p class="abs card-text">I am an Intellectual Property Lawyer and focus on patents, copyrights, trademarks, &amp; trade secrets<br>...</p>
      <div class="abs card-rule"></div>
      <div class="abs read-more" style="left:96px">read more</div>
    </article>

    <article class="abs card" style="left:341px">
      <div class="abs card-photo photo-bulbs" role="img" aria-label="Photo of one glowing energy-saving bulb among unlit light bulbs"></div>
      <div class="abs card-strip"></div>
      <svg class="abs card-notch" width="14" height="8" viewBox="0 0 14 8" aria-hidden="true"><polygon points="0,0 14,0 7,8" fill="#1b8be0"/></svg>
      <h2 class="abs card-title">Why Us?</h2>
      <p class="abs card-text">Lorem ipsum dolor sit amet, consectetur adipiscing elit. Curabitur lacinia pretium risus ac euismod.</p>
      <div class="abs card-rule"></div>
      <div class="abs read-more" style="left:95px">read more</div>
    </article>

    <article class="abs card" style="left:647px">
      <div class="abs card-photo photo-news" role="img" aria-label="Photo of a newspaper, keyboard and a cup of coffee"></div>
      <div class="abs card-strip"></div>
      <svg class="abs card-notch" width="14" height="8" viewBox="0 0 14 8" aria-hidden="true"><polygon points="0,0 14,0 7,8" fill="#1b8be0"/></svg>
      <h2 class="abs card-title">Latest News</h2>
      <p class="abs card-text">Lorem ipsum dolor sit amet, consectetur adipiscing elit. Curabitur lacinia.</p>
      <div class="abs card-rule"></div>
      <div class="abs read-more" style="left:96px">read more</div>
    </article>
  </section>

  <footer class="abs site-footer">
    <div class="abs copyright">Copyright 2013 · All rights reserved</div>
    <div class="abs footer-links">Sitemap<span class="sep">|</span>FAQ<span class="sep">|</span>Privacy Policy</div>
  </footer>
</body>
</html>
```